Healthy Meal Delivery Website Needs to be updated, current, fresh and modern

Hi there,

The current website i have is super old and outdated.

I would like a beautiful modern site that has all the same content as the previous except with a a new, modern and trustworthy feel.

The current website is https://tovalplatefresh.com/

Target Market(s)

Health Conscious Young Professionals

Industry/Entity Type

Food Service

Font styles to use
Sans Serif

Requirements
Must have
• Modern Trustworthy feel
Should not have
• Anything out dated or cheesy or scammy

```html
<!DOCTYPE html>
<html lang="en">
<head>
<meta charset="utf-8">
<title>Toval Plate Fresh – Fresh Diet Meals Delivered</title>
<link rel="stylesheet" href="https://fonts.googleapis.com/css2?family=Ubuntu:wght@300;400;500;700&display=swap">
<style>
:root{
  --blue:#1b8fd6;
  --blue-dark:#1478b8;
  --yellow:#e9e51a;
  --ink:#222;
  --muted:#555;
  --grey-bg:#f2f2f2;
  --footer:#262626;
  --footer-text:#9a9a9a;
  --white:#fff;
}
*{box-sizing:border-box;margin:0;padding:0}
html,body{width:1200px;height:2748px;overflow:hidden}
body{font-family:'Ubuntu',sans-serif;color:var(--ink);background:var(--white);position:relative}
.abs{position:absolute}
.center{text-align:center}

/* header */
.brand{left:104px;top:24px;display:flex;align-items:center;gap:10px;font-size:24px;font-weight:500;color:var(--blue)}
.brand-mark{width:26px;height:26px;border-radius:50%;background:var(--yellow)}
.contact-top{top:22px;display:flex;align-items:center;gap:12px;font-size:15px;color:#333}
.contact-top .ico{width:32px;height:32px;border-radius:50%;background:#e5e5e5;display:flex;align-items:center;justify-content:center}
.main-nav{left:100px;top:82px;width:1000px;height:42px;background:var(--blue);display:flex;align-items:center;padding:0 28px;gap:31px;font-size:14px;color:var(--white);z-index:2}
.main-nav .search{margin-left:auto}

/* hero */
.hero-photo{left:0;top:124px;width:1200px;height:414px;background:radial-gradient(circle at 80% 30%,#c8243d 0,#8f1a2a 18%,transparent 32%),radial-gradient(circle at 25% 80%,#c42a45 0,transparent 22%),linear-gradient(120deg,#7a9a3c,#3c5a1f 40%,#b02238 70%,#6e8f2f)}
.hero-box{left:132px;top:176px;width:502px;height:278px;background:rgba(255,255,255,.82);padding:36px 34px}
.hero-box h1{font-size:31px;font-weight:400;color:#222;margin-bottom:18px}
.hero-box li{list-style:none;display:flex;align-items:center;gap:10px;font-size:14px;margin-bottom:10px;color:#333}
.btn{display:inline-block;border-radius:17px;padding:0 22px;height:33px;line-height:33px;font-size:14px;margin-top:14px;margin-right:10px}
.btn-yellow{background:var(--yellow);color:#222}
.btn-blue{background:var(--blue);color:var(--white)}

/* menu items */
.menu-band{left:0;top:538px;width:1200px;height:398px;background:var(--grey-bg)}
.section-title{width:1200px;left:0;font-size:28px;font-weight:400;text-align:center;color:#222}
.rule{width:170px;left:515px;border-top:2px dotted #bbb}
.lead{left:140px;width:920px;text-align:center;font-size:16px;line-height:23px;color:#333}
.dish{top:696px;width:183px;height:158px;border-radius:4px}
.dot{top:886px;width:10px;height:10px;border-radius:50%;background:#333}

/* testimonials */
.quote{left:280px;width:640px;top:1060px;text-align:center;font-size:14px;line-height:21px;color:#444}
.avatar{left:564px;top:1128px;width:68px;height:68px;border-radius:50%;background:linear-gradient(#d8c3b2,#a5816b)}
.quote-badge{left:614px;top:1158px;width:38px;height:38px;border-radius:50%;background:var(--blue);border:3px solid #fff;color:#fff;font-size:24px;text-align:center;line-height:40px;font-weight:700}
.arrow-side{top:1104px}

/* diet band */
.diet-band{left:0;top:1286px;width:1200px;height:488px;background:linear-gradient(135deg,#2397dc,#1382c8 60%,#2a9de0)}
.diet-band .txt{color:var(--white)}
.feature h3{font-size:22px;font-weight:700;margin-bottom:8px}
.feature p{font-size:12.5px;line-height:19px}
.monitor-frame{left:400px;top:1494px;width:396px;height:250px;background:#111;border-radius:8px 8px 0 0;padding:14px}
.monitor-screen{width:100%;height:100%;background:linear-gradient(135deg,#4c6a22,#2a3314 40%,#7b4a2a 70%,#3e5c1c)}
.monitor-chin{left:400px;top:1744px;width:396px;height:34px;background:linear-gradient(#e8e8e8,#c8c8c8);border-radius:0 0 8px 8px}
.monitor-stand{left:540px;top:1778px;width:116px;height:40px;background:linear-gradient(#d0d0d0,#eaeaea);clip-path:polygon(12% 0,88% 0,100% 100%,0 100%)}

/* intro */
.intro-title{left:180px;width:840px;top:1852px;text-align:center;color:var(--blue);font-size:28px;line-height:32px;font-weight:500}
.card{top:2026px;width:238px;height:279px;border:1px solid #ddd;background:var(--white);text-align:center;padding:20px 16px}
.card.active{background:var(--yellow);border-color:var(--yellow)}
.card svg{display:block;margin:0 auto 14px}
.card h3{font-size:26px;font-weight:500;color:var(--blue);margin-bottom:12px}
.card p{font-size:12.5px;line-height:20px;font-weight:500;color:#222}
.round-btn{top:2354px;width:34px;height:34px;border-radius:50%;background:var(--blue);display:flex;align-items:center;justify-content:center}

/* footer */
.site-footer{left:0;top:2433px;width:1200px;height:315px;background:var(--footer);border-top:4px dotted #444}
.foot-nav{top:2460px;left:0;width:1200px;display:flex;justify-content:center;gap:30px;font-size:14px;color:#ddd}
.foot-col{top:2522px;font-size:13px;line-height:22px;color:var(--footer-text)}
.foot-col h4{font-size:14px;font-weight:400;color:#bbb;margin-bottom:10px}
.social{display:flex;gap:8px;margin-top:4px}
.social span{width:24px;height:24px;border-radius:3px}
.copyright{left:0;width:1200px;top:2702px;text-align:center;font-size:10px;color:#888}
</style>
</head>
<body>

<header>
  <div class="abs brand"><span class="brand-mark"></span>Toval Plate Fresh</div>
  <div class="abs contact-top" style="left:588px">
    <span class="ico"><svg width="14" height="14" viewBox="0 0 24 24"><path fill="#333" d="M6.6 10.8a15 15 0 0 0 6.6 6.6l2.2-2.2c.3-.3.7-.4 1-.2 1.1.4 2.3.6 3.6.6.6 0 1 .4 1 1V20c0 .6-.4 1-1 1A17 17 0 0 1 3 4c0-.6.4-1 1-1h3.5c.6 0 1 .4 1 1 0 1.3.2 2.5.6 3.6.1.3 0 .7-.2 1z"/></svg></span>
    PHONE: (416) 555-0142
  </div>
  <div class="abs contact-top" style="left:830px">
    <span class="ico"><svg width="14" height="12" viewBox="0 0 24 18"><path fill="#333" d="M0 0h24v18H0z"/><path fill="none" stroke="#e5e5e5" stroke-width="2" d="M1 1l11 9 11-9"/></svg></span>
    EMAIL: SALES@TOVALPLATEFRESH.COM
  </div>
  <nav class="abs main-nav">
    <span>HOME</span><span>TOVAL MEAL PLAN</span><span>MENU</span><span>PRICING</span><span>ABOUT</span><span>PRESS</span><span>CONTACT</span><span>SIGN UP</span><span>LOGIN</span>
    <svg class="search" width="14" height="14" viewBox="0 0 24 24"><circle cx="10" cy="10" r="7" fill="none" stroke="#fff" stroke-width="3"/><path d="M15 15l7 7" stroke="#fff" stroke-width="3"/></svg>
  </nav>
</header>

<section>
  <div class="abs hero-photo" role="img" aria-label="Close-up of a fresh salad with raspberries, blueberries and greens"></div>
  <div class="abs hero-box">
    <h1>FRESH DIET MEALS DELIVERED</h1>
    <ul>
      <li><svg width="16" height="12" viewBox="0 0 16 12"><path d="M0 6C3 0 8 0 8 6 4 8 2 8 0 6z M8 6c2-6 7-6 8 0-3 3-6 3-8 0z" fill="var(--blue)"/></svg>Real food you'll love to eat</li>
      <li><svg width="16" height="12" viewBox="0 0 16 12"><path d="M0 6C3 0 8 0 8 6 4 8 2 8 0 6z M8 6c2-6 7-6 8 0-3 3-6 3-8 0z" fill="var(--blue)"/></svg>Portion controlled meals to maximize your weight loss</li>
      <li><svg width="16" height="12" viewBox="0 0 16 12"><path d="M0 6C3 0 8 0 8 6 4 8 2 8 0 6z M8 6c2-6 7-6 8 0-3 3-6 3-8 0z" fill="var(--blue)"/></svg>No grocery shopping, cooking or cleaning required</li>
      <li><svg width="16" height="12" viewBox="0 0 16 12"><path d="M0 6C3 0 8 0 8 6 4 8 2 8 0 6z M8 6c2-6 7-6 8 0-3 3-6 3-8 0z" fill="var(--blue)"/></svg>Freshly prepared by our in house chefs</li>
    </ul>
    <span class="btn btn-yellow">Customer Login</span><span class="btn btn-blue">Sign Up Now</span>
  </div>
</section>

<section>
  <div class="abs menu-band"></div>
  <h2 class="abs section-title" style="top:574px">Select From Over 100 Menu Items</h2>
  <div class="abs rule" style="top:622px"></div>
  <p class="abs lead" style="top:634px">You can choose your own meals from over 100 tasty entrees, desserts and snack foods. You can choose your meals online, or we can select your meals for you.</p>
  <div class="abs dish" style="left:112px;background:linear-gradient(135deg,#e2b23a,#d8452a 55%,#6a9a34)" role="img" aria-label="Scrambled eggs with roasted tomatoes"></div>
  <div class="abs dish" style="left:310px;background:linear-gradient(135deg,#b07a3e,#7a4e24)" role="img" aria-label="Golden waffles"></div>
  <div class="abs dish" style="left:508px;background:linear-gradient(135deg,#5a2d1c,#2e1810 60%,#5c7f2a)" role="img" aria-label="Grilled steak"></div>
  <div class="abs dish" style="left:706px;background:linear-gradient(135deg,#e0a45a,#b26a2a 60%,#8aa83a)" role="img" aria-label="Grilled chicken breasts"></div>
  <div class="abs dish" style="left:904px;background:linear-gradient(135deg,#e8e4c8,#9cc35a 60%,#d4d0b4)" role="img" aria-label="Vegetable wraps"></div>
  <span class="abs dot" style="left:568px"></span>
  <span class="abs dot" style="left:604px"></span>
  <span class="abs dot" style="left:620px"></span>
</section>

<section>
  <h2 class="abs section-title" style="top:988px">Client Testimonials</h2>
  <div class="abs rule" style="top:1034px"></div>
  <p class="abs quote">“Ok, so you know I loved Toval food the first time but somehow, the second time I love it even more. My lentil soup was incredible! And I am looooving these huge snacks - melba, cheese, veggies, turkey pepperoni - I feel like I am able to graze all day log! So brilliant! *”</p>
  <svg class="abs arrow-side" style="left:176px" width="18" height="32" viewBox="0 0 18 32"><path d="M16 2L2 16l14 14" fill="none" stroke="#999" stroke-width="2"/></svg>
  <svg class="abs arrow-side" style="left:982px" width="18" height="32" viewBox="0 0 18 32"><path d="M2 2l14 14L2 30" fill="none" stroke="#999" stroke-width="2"/></svg>
  <div class="abs avatar" role="img" aria-label="Client portrait"></div>
  <div class="abs quote-badge">”</div>
  <p class="abs center" style="left:0;width:1200px;top:1206px;font-size:13px;color:#555">Maren</p>
  <p class="abs center" style="left:0;width:1200px;top:1228px;font-size:13px;color:var(--blue);font-weight:500">Lorium ipsum</p>
</section>

<section>
  <div class="abs diet-band" role="img" aria-label="Soft blue backdrop of a healthy kitchen scene"></div>
  <h2 class="abs txt center" style="left:0;width:1200px;top:1310px;font-size:28px;font-weight:400">The Toval Diet</h2>
  <svg class="abs" style="left:574px;top:1358px" width="52" height="30" viewBox="0 0 52 30"><path d="M6 24a20 20 0 0 1 40 0z M2 26h48" fill="none" stroke="#fff" stroke-width="2"/><circle cx="26" cy="3" r="2" fill="#fff"/></svg>
  <div class="abs txt center feature" style="left:400px;width:400px;top:1398px"><h3>WHAT YOU GET</h3><p>Toval Diet Delivery provides you with 3 fresh daily meals and<br>3 snacks delivered to your doorstep before 6am.</p></div>

  <div class="abs txt feature" style="left:96px;width:240px;top:1500px;text-align:right"><h3>SELECTION</h3><p>Choose your meals from over 100 delicious entrees, snacks and desserts.</p></div>
  <div class="abs txt feature" style="left:96px;width:240px;top:1612px;text-align:right"><h3>LUXURY</h3><p>Enjoy the luxury of having your own personal chef and nutritionist prepare Toval Diet meals for you.</p></div>
  <div class="abs txt feature" style="left:858px;width:250px;top:1500px"><h3>WHAT IS PHASE 1?</h3><p>Phase 1 is the stricter phase that eliminates bad carbs and processed foods; no sugar, candy, pasta or bread.</p></div>
  <div class="abs txt feature" style="left:858px;width:250px;top:1612px"><h3>WHAT IS PHASE 2?</h3><p>Phase 2 reintroduces certain healthy carbs into your diet - whole grains, rice and potatoes, providing you with a greater variety of meals.</p></div>
  <svg class="abs" style="left:816px;top:1504px" width="24" height="24" viewBox="0 0 24 24"><path d="M22 2L2 12l20 10z" fill="none" stroke="#fff" stroke-width="2"/></svg>
  <svg class="abs" style="left:816px;top:1616px" width="24" height="24" viewBox="0 0 24 24"><path d="M22 2L2 12l20 10z" fill="none" stroke="#fff" stroke-width="2"/></svg>
  <svg class="abs" style="left:342px;top:1502px" width="36" height="28" viewBox="0 0 36 28"><circle cx="8" cy="14" r="6" fill="none" stroke="#fff" stroke-width="2"/><circle cx="24" cy="6" r="4" fill="none" stroke="#fff" stroke-width="2"/><circle cx="26" cy="22" r="4" fill="none" stroke="#fff" stroke-width="2"/></svg>
  <svg class="abs" style="left:344px;top:1614px" width="30" height="24" viewBox="0 0 30 24"><path d="M2 8l6-6h14l6 6-13 14z M2 8h26" fill="none" stroke="#fff" stroke-width="2"/></svg>

  <div class="abs monitor-frame"><div class="monitor-screen" role="img" aria-label="Stir-fried beef with broccoli and peppers"></div></div>
  <div class="abs monitor-chin"></div>
  <div class="abs monitor-stand"></div>
</section>

<section>
  <h2 class="abs intro-title">THE TOVAL DIET DELIVERS DIET MEALS TO YOUR DOOR IN TORONTO, GTA AND MONTREAL</h2>
  <p class="abs lead" style="top:1938px">Our fresh and delicious diet meals and snacks are made with only the best natural ingredients that nourish your body. Why not let us prepare your meals while you lose the weight?</p>

  <article class="abs card" style="left:99px">
    <svg width="50" height="60" viewBox="0 0 50 60"><circle cx="25" cy="36" r="20" fill="none" stroke="var(--blue)" stroke-width="2.5"/><path d="M25 16c0-6 4-10 10-12" fill="none" stroke="var(--blue)" stroke-width="2.5"/></svg>
    <h3>HEALTHY</h3><p>The Toval Diet is a great way to ensure you are eating all the nutrients you need, and nothing your body doesn't need.</p>
  </article>
  <article class="abs card active" style="left:354px">
    <svg width="60" height="60" viewBox="0 0 60 60"><circle cx="30" cy="30" r="26" fill="none" stroke="var(--blue)" stroke-width="2.5"/><path d="M18 30l9 9 16-18" fill="none" stroke="var(--blue)" stroke-width="3"/></svg>
    <h3>CHOICE</h3><p>You can choose your own meals from over 100 tasty entrees, desserts and snack foods. You can choose your meals online, or we can select your meals for you.</p>
  </article>
  <article class="abs card" style="left:609px">
    <svg width="60" height="60" viewBox="0 0 60 60"><path d="M6 10h32L22 30z M22 30v22 M12 54h20" fill="none" stroke="var(--blue)" stroke-width="2.5"/><circle cx="44" cy="14" r="8" fill="none" stroke="var(--blue)" stroke-width="2.5"/></svg>
    <h3>FRESH</h3><p>All of our meals are real food, freshly prepared by our in-house expert chefs.</p>
  </article>
  <article class="abs card" style="left:864px">
    <svg width="60" height="60" viewBox="0 0 60 60"><circle cx="30" cy="30" r="9" fill="none" stroke="var(--blue)" stroke-width="2.5"/><circle cx="30" cy="30" r="19" fill="none" stroke="var(--blue)" stroke-width="6" stroke-dasharray="7 5"/></svg>
    <h3>CUSTOMIZED</h3><p>Your meals will be delivered fresh to your door, customized for your unique body type and level of activity.</p>
  </article>

  <span class="abs round-btn" style="left:560px"><svg width="10" height="14" viewBox="0 0 10 14"><path d="M8 1L2 7l6 6" fill="none" stroke="#fff" stroke-width="2.5"/></svg></span>
  <span class="abs round-btn" style="left:604px"><svg width="10" height="14" viewBox="0 0 10 14"><path d="M2 1l6 6-6 6" fill="none" stroke="#fff" stroke-width="2.5"/></svg></span>
</section>

<footer>
  <div class="abs site-footer"></div>
  <nav class="abs foot-nav"><span>HOME</span><span>TOVAL MEAL PLAN</span><span>MENU</span><span>PRICING</span><span>ABOUT</span><span>PRESS</span><span>CONTACT</span><span>SIGN UP</span><span>LOGIN</span></nav>
  <div class="abs foot-col" style="left:134px">
    <h4>&#9679; Contact Us</h4>
    <p>Toronto: 416-555-0142</p>
    <p>&#9993; sales@tovalplatefresh.com</p>
  </div>
  <div class="abs foot-col" style="left:485px;width:250px">
    <h4 style="color:#ddd">What is Toval ?</h4>
    <p>Toval is the Toronto &amp; Montreal Diet Delivery program based on the Toval Plan™, healthy carbs and the right fats.</p>
    <p style="margin-top:24px;color:var(--yellow)">more &#9679;</p>
  </div>
  <div class="abs foot-col" style="left:828px">
    <h4>Follow Us</h4>
    <div class="social">
      <span style="background:#3b5998"></span><span style="background:#2fa8d8"></span><span style="background:#1f6fa8"></span><span style="background:#ddd"></span><span style="background:#777"></span><span style="background:#555"></span><span style="background:#c8232c"></span>
    </div>
  </div>
  <p class="abs copyright">© 2018 • www.tovalplatefresh.com • PRIVACY POLICY</p>
</footer>

</body>
</html>
```